Polling website project

We need a website design for a polling website called votrik.net. This will be a website where visitors can take and create polls for various topics along with view results. We want something really simple and "web 2.0." We are going to make a cell phone app that goes along with the website and we want the look and feel of the website to be very "app-like." Basically that means minimalistic design with a poll being the center of the page.
When someone comes to the site, we want them to see basically just a poll in the center of the screen and a toolbar at the top of the page with links to login fields/user profile, post a new poll, view friends list, a drop-down list of poll topics, and a search bar. We need about three pages mocked up: a home page/poll view page, a user control panel/profile page, a submit new poll page.
We also want our logo/header to have a "pulse" theme. The name votrik is supposed to be a play on the word pulse, we'd like the logo to make that obvious, maybe the use of the EKG graph could work.
We also want a nice tab in the corner to sign up that is attractive and flashy, kind of like the feedback tab on the side of this website.
Updates
Target Market(s)
Teens and young adults, the chatnook crowd
Industry/Entity Type
Cell Phone
Look and feel
Each slider illustrates characteristics of the customer's brand and the style your logo design should communicate.

```html
<!DOCTYPE html>
<html lang="en">
<head>
<meta charset="utf-8">
<title>votrik.net – Poll results</title>
<link rel="stylesheet" href="https://fonts.googleapis.com/css2?family=Arimo:ital,wght@0,400;0,700;1,400&display=swap">
<style>
  :root {
    --page-bg: #f2f2f2;
    --panel-blue: #abdcf5;
    --nav-grey: #bcbdc0;
    --logo-grey: #808184;
    --ink: #231f20;
    --white: #ffffff;
    --tone-1: #3a3a3b;
    --tone-2: #5e5f62;
    --tone-3: #939598;
    --tone-4: #a7a9ac;
    --muted-label: #b9babc;
    --rule-grey: #8a8b8d;
  }
  * { box-sizing: border-box; margin: 0; padding: 0; }
  html, body {
    width: 1200px; height: 886px; overflow: hidden;
    background: var(--page-bg);
    font-family: "Arimo", Arial, sans-serif;
    color: var(--ink);
  }
  .canvas { position: relative; width: 1200px; height: 886px; }
  .panel {
    position: absolute; left: 5px; top: 41px; width: 933px; height: 809px;
    background: var(--panel-blue);
    border-bottom: 3px solid var(--rule-grey);
  }
  .nav {
    position: absolute; top: 41px; height: 100px; width: 256px;
    background: var(--nav-grey);
    color: var(--white); font-size: 18.5px; text-align: center;
  }
  .nav--left { left: 5px; }
  .nav--right { left: 681px; width: 257px; }
  .nav__link { position: absolute; left: 0; right: 0; line-height: 22px; white-space: nowrap; }
  .nav__rule { position: absolute; height: 1px; background: var(--white); }
  .logo-block {
    position: absolute; left: 261px; top: 8px; width: 420px; height: 133px;
    background: var(--logo-grey);
    color: var(--white); font-size: 33px; text-align: center; line-height: 128px;
  }
  .question {
    position: absolute; left: 87px; top: 180px;
    font-size: 21px; font-weight: 700; white-space: nowrap;
  }
  .question-arrow { position: absolute; left: 34px; top: 182px; }
  .divider { position: absolute; left: 431px; top: 150px; width: 1px; height: 98px; background: var(--ink); }
  .formula-key {
    position: absolute; left: 466px; top: 175px; width: 36px; height: 37px;
    background: var(--ink); color: var(--white);
    font-size: 20px; font-weight: 700; text-align: center; line-height: 37px;
  }
  .formula-equals { position: absolute; left: 517px; top: 185px; width: 23px; }
  .formula-equals span { display: block; height: 6px; background: var(--ink); margin-bottom: 4px; border-radius: 1px; }
  .fraction { position: absolute; left: 556px; top: 159px; width: 171px; text-align: center; font-size: 20.5px; font-weight: 700; }
  .fraction__line { height: 2px; background: var(--ink); margin: 6px 0 6px; }
  .donut { position: absolute; left: 60px; top: 280px; }
  .donut-label { position: absolute; font-size: 19px; font-weight: 700; }
  .region-map {
    position: absolute; left: 440px; top: 312px; width: 458px; height: 274px;
    border-radius: 18px 40px 60px 30px;
    background: linear-gradient(135deg, #8e8f92 0%, #6b6c6f 45%, #4b4c4e 100%);
  }
  .share { position: absolute; top: 569px; width: 84px; text-align: center; }
  .share__badge {
    width: 84px; height: 84px; border-radius: 50%;
    background: var(--ink); color: var(--white);
    font-size: 39px; font-weight: 700; line-height: 86px; letter-spacing: -1px;
  }
  .share__badge sup { font-size: 15px; vertical-align: 18px; margin-left: 1px; }
  .share__figure {
    margin: 4px auto 0; width: 76px; height: 118px; border-radius: 10px;
    background: #e3f3fc;
  }
  .share--men { left: 239px; }
  .share--women { left: 350px; }
  .age-legend { position: absolute; left: 556px; top: 608px; }
  .age-bar {
    position: absolute; left: 0; height: 25px; padding-left: 9px;
    font-size: 17px; font-weight: 700; line-height: 25px; white-space: nowrap;
  }
  .age-bar .arrow { display: inline-block; vertical-align: -1px; margin: 0 1px; }
  .age-bar--under18 { top: 0; width: 74px; background: var(--tone-3); }
  .age-bar--18-29 { top: 39px; width: 119px; background: var(--tone-4); }
  .age-bar--30-45 { top: 76px; width: 172px; background: var(--tone-2); color: var(--muted-label); }
  .age-bar--50-64 { top: 111px; width: 218px; background: var(--tone-1); color: var(--muted-label); }
  .age-bar--65up { top: 147px; width: 56px; background: var(--white); }
</style>
</head>
<body>
<div class="canvas">
  <div class="panel"></div>

  <nav class="nav nav--left">
    <span class="nav__link" style="top:17px">CATEGORIES</span>
    <span class="nav__rule" style="left:15px; width:228px; top:48px"></span>
    <span class="nav__link" style="top:59px">SUBMIT QUESTION</span>
  </nav>
  <div class="logo-block">LOGO</div>
  <nav class="nav nav--right">
    <span class="nav__link" style="top:21px">SIGN UP / SIGN IN</span>
    <span class="nav__rule" style="left:14px; width:227px; top:51px"></span>
    <span class="nav__link" style="top:60px">FRIEND’S LIST</span>
  </nav>

  <svg class="question-arrow" width="32" height="22" viewBox="0 0 32 22" aria-hidden="true">
    <path d="M1 11 H29 M19 2 L29 11 L19 20" fill="none" stroke="#231f20" stroke-width="2.6"/>
  </svg>
  <h1 class="question">How often do people orgasm?</h1>
  <div class="divider"></div>
  <div class="formula-key">%</div>
  <div class="formula-equals"><span></span><span></span></div>
  <div class="fraction">
    <div>orgasm</div>
    <div class="fraction__line"></div>
    <div># of sex</div>
  </div>

  <svg class="donut" width="290" height="280" viewBox="0 0 290 280">
    <g transform="translate(145 140) rotate(-90)" fill="none" stroke-width="23">
      <circle r="91.5" pathLength="360" stroke="#ffffff" stroke-dasharray="104 360" stroke-dashoffset="-241"/>
      <circle r="91.5" pathLength="360" stroke="#939598" stroke-dasharray="76.5 360" stroke-dashoffset="-164.5"/>
      <circle r="91.5" pathLength="360" stroke="#5e5f62" stroke-dasharray="164.5 360" stroke-dashoffset="0"/>
      <circle r="91.5" pathLength="360" stroke="#3a3a3b" stroke-dasharray="15 360" stroke-dashoffset="-345"/>
    </g>
    <circle cx="145" cy="140" r="78" fill="#abdcf5" stroke="#231f20" stroke-width="5"/>
    <text x="145" y="134" text-anchor="middle" font-family="Arimo, Arial, sans-serif" font-size="25" font-weight="700" fill="#231f20">%</text>
    <text x="145" y="151" text-anchor="middle" font-family="Arimo, Arial, sans-serif" font-size="19.5" font-style="italic" fill="#231f20">of the time</text>
  </svg>
  <span class="donut-label" style="left:165px; top:286px">100</span>
  <span class="donut-label" style="left:247px; top:295px">75</span>
  <span class="donut-label" style="left:316px; top:437px">50</span>
  <span class="donut-label" style="left:141px; top:527px">25</span>
  <span class="donut-label" style="left:71px; top:371px">0</span>

  <div class="region-map" role="img" aria-label="Map of US states shaded by how often people orgasm"></div>

  <div class="share share--men">
    <div class="share__badge">75<sup>%</sup></div>
    <div class="share__figure" role="img" aria-label="Male figure pictogram"></div>
  </div>
  <div class="share share--women">
    <div class="share__badge">25<sup>%</sup></div>
    <div class="share__figure" role="img" aria-label="Female figure pictogram"></div>
  </div>

  <div class="age-legend">
    <div class="age-bar age-bar--under18"><svg class="arrow" width="14" height="12" viewBox="0 0 14 12" aria-hidden="true"><path d="M13 6H2M7 1.5L2 6L7 10.5" stroke="currentColor" stroke-width="2.4" fill="none"/></svg>18</div>
    <div class="age-bar age-bar--18-29">18<svg class="arrow" width="14" height="12" viewBox="0 0 14 12" aria-hidden="true"><path d="M1 6H12M7 1.5L12 6L7 10.5" stroke="currentColor" stroke-width="2.4" fill="none"/></svg>29</div>
    <div class="age-bar age-bar--30-45">30<svg class="arrow" width="14" height="12" viewBox="0 0 14 12" aria-hidden="true"><path d="M1 6H12M7 1.5L12 6L7 10.5" stroke="currentColor" stroke-width="2.4" fill="none"/></svg>45</div>
    <div class="age-bar age-bar--50-64">50<svg class="arrow" width="14" height="12" viewBox="0 0 14 12" aria-hidden="true"><path d="M1 6H12M7 1.5L12 6L7 10.5" stroke="currentColor" stroke-width="2.4" fill="none"/></svg>64</div>
    <div class="age-bar age-bar--65up">65 <svg class="arrow" width="14" height="12" viewBox="0 0 14 12" aria-hidden="true"><path d="M1 6H12M7 1.5L12 6L7 10.5" stroke="currentColor" stroke-width="2.4" fill="none"/></svg></div>
  </div>
</div>
</body>
</html>
```